Homemaking training schools needs a Business Card design

Designer, Hello!

No special requirements, good-looking enough.
--------------------------------------------------------------------------

Name: Marcus Dole
Chairman
Tel: 0574-71948263
Mobile: 13857420916
Email: kelvora@mailnest.example
Web: www.prt2019.example
Add: No.258, LanpingJie, BeiyuanQu, Ningbo, Zhejiang

LOGO
Ningbo PRT Homemaking Training School

Target Market(s)

pregnant women, mothers, infants, the elderly and families, including cleaning, cooking, nursing training.

Industry/Entity Type

Business

Contact Information for Business Card

Name: Marcus Dole
Chairman
Tel: 0574-71948263
Mobile: 13857420916
Email: kelvora@mailnest.example
Web: www.prt2019.example

LOGO

Font styles to use
Serif
Sans Serif
Decorative

Requirements
Nice to have
• Feels: clean, specifications, safety, comfort, warmth and happiness.

```html
<!DOCTYPE html>
<html lang="en">
<head>
<meta charset="utf-8">
<title>PeiRuiTang Business Card</title>
<link rel="stylesheet" href="https://fonts.googleapis.com/css2?family=Jost:ital,wght@0,400;0,500;0,700;1,400&display=swap">
<style>
  :root {
    --brand-blue: #0a74bb;
    --brand-pink: #ea0a8c;
    --ink: #3a3a3a;
    --paper: #ffffff;
    --backdrop: #ecebe9;
  }
  * { margin: 0; padding: 0; box-sizing: border-box; }
  html, body { width: 1200px; height: 1194px; overflow: hidden; }
  body {
    background: var(--backdrop);
    font-family: "Jost", sans-serif;
    position: relative;
  }
  .card {
    position: absolute;
    width: 794px;
    height: 514px;
    box-shadow: 0 6px 18px rgba(0,0,0,0.18);
    overflow: hidden;
  }
  .card-front { left: 216px; top: 56px; background: var(--paper); }
  .card-back { left: 214px; top: 622px; background: var(--brand-blue); color: var(--paper); }

  .brand {
    position: absolute;
    display: flex;
    flex-direction: column;
    align-items: center;
  }
  .brand-name { font-weight: 500; line-height: 1; letter-spacing: -0.5px; }
  .brand-tagline { font-weight: 400; line-height: 1; }

  .card-front .brand { left: 0; right: 0; top: 250px; }
  .card-front .brand-name { font-size: 56px; color: var(--brand-blue); }
  .card-front .brand-tagline { font-size: 20px; color: var(--ink); margin-top: 10px; }

  .card-back .brand { left: 560px; width: 200px; top: 104px; }
  .card-back .brand-name { font-size: 26px; color: var(--paper); }
  .card-back .brand-tagline { font-size: 9.5px; color: var(--paper); margin-top: 4px; }

  .accent-band { position: absolute; left: 0; top: 0; }

  .contact-list { position: absolute; left: 80px; top: 82px; list-style: none; }
  .contact-item { display: flex; align-items: center; height: 46px; margin-bottom: 10px; }
  .contact-item.address { height: 48px; margin-top: 6px; }
  .contact-icon {
    width: 61px; height: 46px; background: var(--paper);
    display: flex; align-items: center; justify-content: center; flex-shrink: 0;
  }
  .contact-item.address .contact-icon { height: 48px; }
  .contact-text { margin-left: 32px; font-size: 22px; letter-spacing: 0.6px; line-height: 1.35; }
  .website {
    position: absolute; left: 80px; top: 330px;
    font-size: 25px; font-style: italic; letter-spacing: 0.5px;
  }
  .holder { position: absolute; right: 76px; top: 382px; text-align: right; }
  .holder-name { font-size: 48px; font-weight: 700; letter-spacing: 1.5px; line-height: 1; }
  .holder-title { font-size: 31px; font-weight: 700; letter-spacing: 1px; line-height: 1; margin-top: 6px; }
</style>
</head>
<body>
  <section class="card card-front">
    <div class="brand">
      <span class="brand-name">PeiRuiTang</span>
      <span class="brand-tagline">Training &amp; Services</span>
    </div>
  </section>

  <section class="card card-back">
    <svg class="accent-band" width="794" height="514" viewBox="0 0 794 514" aria-hidden="true">
      <polygon points="384,360 794,360 794,514 268,514" fill="var(--brand-pink)"/>
    </svg>

    <div class="brand">
      <span class="brand-name">PeiRuiTang</span>
      <span class="brand-tagline">Training &amp; Services</span>
    </div>

    <ul class="contact-list">
      <li class="contact-item">
        <span class="contact-icon">
          <svg width="18" height="26" viewBox="0 0 18 26" aria-hidden="true"><rect x="2" y="1.5" width="14" height="23" rx="2" fill="none" stroke="var(--brand-blue)" stroke-width="2.4"/><line x1="2" y1="20" x2="16" y2="20" stroke="var(--brand-blue)" stroke-width="2"/></svg>
        </span>
        <span class="contact-text">13857420916</span>
      </li>
      <li class="contact-item">
        <span class="contact-icon">
          <svg width="30" height="20" viewBox="0 0 30 20" aria-hidden="true"><rect x="1" y="1" width="28" height="18" fill="none" stroke="var(--brand-blue)" stroke-width="2"/><polyline points="1,1 15,12 29,1" fill="none" stroke="var(--brand-blue)" stroke-width="2"/><line x1="1" y1="19" x2="11" y2="9" stroke="var(--brand-blue)" stroke-width="1.6"/><line x1="29" y1="19" x2="19" y2="9" stroke="var(--brand-blue)" stroke-width="1.6"/></svg>
        </span>
        <span class="contact-text">kelvora@mailnest.example</span>
      </li>
      <li class="contact-item">
        <span class="contact-icon">
          <svg width="26" height="26" viewBox="0 0 24 24" aria-hidden="true"><path d="M6.6 10.8c1.4 2.8 3.8 5.1 6.6 6.6l2.2-2.2c.3-.3.7-.4 1-.2 1.1.4 2.3.6 3.6.6.6 0 1 .4 1 1V20c0 .6-.4 1-1 1C10.6 21 3 13.4 3 4c0-.6.4-1 1-1h3.5c.6 0 1 .4 1 1 0 1.3.2 2.5.6 3.6.1.3 0 .7-.2 1z" fill="var(--brand-blue)"/></svg>
        </span>
        <span class="contact-text">0574-71948263</span>
      </li>
      <li class="contact-item address">
        <span class="contact-icon">
          <svg width="28" height="28" viewBox="0 0 28 28" aria-hidden="true"><circle cx="14" cy="14" r="12" fill="none" stroke="var(--brand-blue)" stroke-width="2.4"/><ellipse cx="14" cy="14" rx="5" ry="12" fill="none" stroke="var(--brand-blue)" stroke-width="1.8"/><line x1="2" y1="14" x2="26" y2="14" stroke="var(--brand-blue)" stroke-width="1.8"/></svg>
        </span>
        <span class="contact-text">No.258, LanpingJie, BeiyuanQu,<br>Ningbo, Zhejiang</span>
      </li>
    </ul>

    <p class="website">www.prt2019.example</p>

    <div class="holder">
      <p class="holder-name">MARCUS DOLE</p>
      <p class="holder-title">CHAIRMAN</p>
    </div>
  </section>
</body>
</html>
```